Communication and Marketing agency needs a new presentation card

We are a group of communication and marketing agencies specialized in companies that are in the logistics and industrial sector. The head agency is TELVANO Grupo and the group consists of 4 agencies: TELVANO Media, TELVANO Digital, TELVANO Research and DifundeEnPantalla. We hace 4 offices in Spain (Madrid, Barcelona, Valencia and Murcia). We are looking for a clean and attractive design that transmits our experience, brand presence in the market and knowledge to those who receive the card.It has to maintain the colors of the logo that is attached.
Target Market(s)
logistics and industrial sector
Marketing department
Contact Information for Business Card
Clean and attractive design

```html
<!DOCTYPE html>
<html lang="en">
<head>
<meta charset="utf-8">
<title>TELVANO Grupo – Business Card</title>
<link rel="stylesheet" href="https://fonts.googleapis.com/css2?family=Open+Sans:wght@300;400;600&family=Tinos:wght@400;700&display=swap">
<style>
  :root {
    --brand-red: #b02a30;
    --brand-red-light: #c0454a;
    --brand-grey: #535558;
    --brand-grey-light: #68696c;
    --paper: #f4f4f4;
    --ink: #3c3c3e;
    --backdrop: #dde1e6;
    --backdrop-edge: #b9c2cd;
  }
  * { box-sizing: border-box; margin: 0; padding: 0; }
  html, body { width: 1200px; height: 675px; overflow: hidden; }
  body {
    background: radial-gradient(ellipse at 40% 60%, var(--backdrop) 0%, var(--backdrop-edge) 100%);
    font-family: "Open Sans", sans-serif;
    position: relative;
  }
  .card {
    position: absolute;
    top: 187px;
    width: 520px;
    height: 300px;
    background: var(--paper);
    overflow: hidden;
    box-shadow: 0 8px 24px rgba(40, 50, 65, 0.25);
  }
  .card--front { left: 45px; }
  .card--back { left: 635px; }

  /* Front */
  .front__red {
    position: absolute;
    left: 210px; top: 0; right: 0; bottom: 0;
    background: linear-gradient(160deg, var(--brand-red-light), var(--brand-red));
  }
  .front__identity {
    position: absolute;
    top: 22px; right: 40px;
    font-family: "Tinos", serif;
    color: #fff;
    text-align: center;
  }
  .front__name { font-weight: 700; font-size: 20px; letter-spacing: 0.5px; }
  .front__position { font-size: 15px; }
  .front__logo-block {
    position: absolute;
    left: 170px; bottom: 0;
    width: 190px; height: 110px;
    background: var(--brand-grey);
    display: flex; align-items: center; justify-content: center;
  }
  .brand-mark {
    font-family: "Open Sans", sans-serif;
    font-weight: 300;
    letter-spacing: 1px;
    white-space: nowrap;
  }
  .front__logo-block .brand-mark { color: #fff; font-size: 20px; }
  .agency-list {
    position: absolute;
    left: 180px; top: 12px;
    width: 26px;
    display: flex; flex-direction: column; align-items: center; gap: 10px;
  }
  .agency-list .brand-mark {
    writing-mode: vertical-rl;
    font-size: 6px;
    letter-spacing: 0.3px;
    color: var(--brand-grey);
  }
  .agency-list .brand-mark--accent { color: var(--brand-red); }
  .contact {
    position: absolute;
    left: 16px; top: 18px;
    height: 240px;
    writing-mode: vertical-rl;
    list-style: none;
    font-size: 12px;
    color: var(--ink);
    display: flex; flex-direction: column; gap: 2px;
  }
  .contact__item { display: flex; align-items: center; gap: 6px; line-height: 1.45; white-space: nowrap; }
  .contact__icon { width: 13px; height: 13px; flex: none; }

  /* Back */
  .back__grey {
    position: absolute;
    left: 0; top: 0; bottom: 0; width: 63%;
    background: linear-gradient(170deg, var(--brand-grey-light), var(--brand-grey));
  }
  .back__bar {
    position: absolute;
    left: 63%; top: 28%; bottom: 0; width: 30px;
    background: var(--brand-red);
  }
  .back__logo {
    position: absolute;
    left: 73%; right: 0; top: 0; bottom: 0;
    display: flex; align-items: center; justify-content: center;
  }
  .back__logo .brand-mark {
    color: var(--brand-red);
    font-size: 30px;
    writing-mode: vertical-rl;
  }
</style>
</head>
<body>

  <section class="card card--front" aria-label="Business card front">
    <ul class="contact">
      <li class="contact__item">
        <svg class="contact__icon" viewBox="0 0 14 14"><circle cx="7" cy="7" r="7" fill="var(--brand-red)"/><path d="M4.5 3.5l1.5 0 .6 2-1 .8a5 5 0 0 0 2.1 2.1l.8-1 2 .6v1.5c0 .5-.4.8-.9.8A6 6 0 0 1 3.7 4.4c0-.5.3-.9.8-.9z" fill="#fff"/></svg>
        <span>Office : +0.000.000.0000</span>
      </li>
      <li class="contact__item">
        <svg class="contact__icon" viewBox="0 0 14 14"><circle cx="7" cy="7" r="7" fill="var(--brand-red)"/><rect x="5" y="3" width="4" height="8" rx="0.8" fill="#fff"/></svg>
        <span>Cell &nbsp;&nbsp;: +0.000.000.0000</span>
      </li>
      <li class="contact__item">
        <svg class="contact__icon" viewBox="0 0 14 14"><circle cx="7" cy="7" r="7" fill="var(--brand-red)"/><rect x="3.5" y="4.5" width="7" height="5" fill="#fff"/><path d="M3.5 4.5l3.5 3 3.5-3" stroke="var(--brand-red)" stroke-width="0.8" fill="none"/></svg>
        <span>info@telvanogrupo.com</span>
      </li>
      <li class="contact__item">
        <svg class="contact__icon" viewBox="0 0 14 14"><circle cx="7" cy="7" r="7" fill="var(--brand-red)"/><circle cx="7" cy="7" r="3.5" fill="none" stroke="#fff" stroke-width="1"/><path d="M3.5 7h7M7 3.5v7" stroke="#fff" stroke-width="0.8"/></svg>
        <span>www.telvanogrupo.com</span>
      </li>
      <li class="contact__item">
        <svg class="contact__icon" viewBox="0 0 14 14"><circle cx="7" cy="7" r="7" fill="var(--brand-red)"/><path d="M7 3a2.6 2.6 0 0 1 2.6 2.6C9.6 7.6 7 11 7 11S4.4 7.6 4.4 5.6A2.6 2.6 0 0 1 7 3z" fill="#fff"/></svg>
        <span>Office Address</span>
      </li>
    </ul>

    <div class="agency-list">
      <span class="brand-mark">TELVANO Media</span>
      <span class="brand-mark">TELVANO Digital</span>
      <span class="brand-mark brand-mark--accent">TELVANO Research</span>
    </div>

    <div class="front__red">
      <div class="front__identity">
        <p class="front__name">Your Name</p>
        <p class="front__position">Position</p>
      </div>
    </div>

    <div class="front__logo-block">
      <span class="brand-mark">TELVANO Grupo</span>
    </div>
  </section>

  <section class="card card--back" aria-label="Business card back">
    <div class="back__grey"></div>
    <div class="back__bar"></div>
    <div class="back__logo">
      <span class="brand-mark">TELVANO Grupo</span>
    </div>
  </section>

</body>
</html>
```